I need a business card design for a new dance business. I offer classical Indian dance tuition and also professional performances. I want to offer the community a variety of Indian dance experiences which include: group class and private tuition, school and preschool educational courses and workshops. dance theatre performances, community function workshops and performances, Kids Bollywood parties, wedding & conference performances, mouth percussion classes, Indian mythology/ dance costume and make up workshops.
The final design should communicate a feeling and impression of the vibrance and energy of Indian dance.
Updates
Hi Everyone,
Project Deadline Extended
Reason: I would like to refine a few changes to the details of this lovely design and we have run out of time!
Project Deadline Extended
Reason: Still waiting to hear back form designer re two possible changes to the card design. Tomorrow is the deadline and I have sent several messages but with no response. I need to see this through before selecting this lovely design.
Thank you.
Tara
Industry/Entity Type
Preschool
Requirements
Must have
- The front of the business card should have the photo of me (my face and torso), surrounded entirely by a border of bright magenta (to match the magenta of my lipstick - it is the same as the magenta on my skirt in the second photo). Within the top border I want (perhaps yellow-gold) writing to say "Tara Holloway - Artistic Director" and within the bottom border it should read "Saffron Lantern Indian Dance." If you turn the card on its side the left border should have my telephone number: 0417 862 493 and the right-hand border should read: saffronlanternindiandance@quillmail.example
The reverse of the card should be the orange of the dance costume
and I'd like the picture of my feet and legs to be on the right side of the back of the card as a side border. Centre-aligned on the orange background it should read (perhaps in dark magenta):
Indian dance classes + private tuition
School + preschool educational courses and workshops
Dance theatre performances
Community function workshops and performances
Children's Bollywood parties
Wedding + conference performances
Mouth percussion classes
Indian mythology and dance demonstration workshops
Dance costume and make-up workshops
Nice to have
- A lovely artistic but easy-to-read font would be nice.

```html
<!DOCTYPE html>
<html lang="en">
<head>
<meta charset="utf-8">
<title>Saffron Lantern Indian Dance — Business Card Reverse</title>
<link rel="stylesheet" href="https://fonts.googleapis.com/css2?family=Kurale&display=swap">
<style>
  :root {
    --page-bg: #ffffff;
    --saffron: #e2671a;
    --saffron-deep: #d4590f;
    --magenta-dark: #5e1238;
    --photo-violet: #7a1f7a;
    --photo-magenta: #b02a9c;
    --photo-gold: #d9913a;
    --photo-shade: #3a1830;
  }
  * { margin: 0; padding: 0; box-sizing: border-box; }
  html, body {
    width: 1200px;
    height: 900px;
    overflow: hidden;
    background: var(--page-bg);
  }
  .canvas {
    position: relative;
    width: 1200px;
    height: 900px;
  }
  .card-back {
    position: absolute;
    left: 134px;
    top: 154px;
    width: 940px;
    height: 590px;
    display: flex;
    background: var(--saffron);
  }
  .services {
    flex: 1;
    display: flex;
    align-items: center;
    justify-content: center;
    background: radial-gradient(circle at 50% 50%, var(--saffron) 0%, var(--saffron-deep) 100%);
  }
  .service-list {
    list-style: none;
    text-align: center;
    font-family: "Kurale", serif;
    font-size: 22px;
    line-height: 42px;
    color: var(--magenta-dark);
    margin-top: -62px;
  }
  .dancer-photo {
    width: 294px;
    height: 100%;
    background:
      linear-gradient(180deg, var(--photo-shade) 0%, rgba(58,24,48,0) 22%),
      linear-gradient(160deg, var(--photo-violet) 0%, var(--photo-magenta) 38%, var(--photo-gold) 62%, var(--photo-magenta) 80%, var(--photo-shade) 100%);
  }
</style>
</head>
<body>
  <main class="canvas">
    <section class="card-back">
      <div class="services">
        <ul class="service-list">
          <li>Indian dance classes + private tuition</li>
          <li>School + preschool educational courses and workshops</li>
          <li>Dance theatre performances</li>
          <li>Community function workshops and performances</li>
          <li>Children's Bollywood parties</li>
          <li>Wedding + conference performances</li>
          <li>Mouth percussion classes</li>
          <li>Indian mythology and dance demonstration workshops</li>
          <li>Dance costume and make-up workshops</li>
        </ul>
      </div>
      <div class="dancer-photo" role="img" aria-label="Photograph of a dancer's legs and feet in a magenta and gold classical Indian dance costume with ankle bells"></div>
    </section>
  </main>
</body>
</html>
```